Novexa company website, a website for employment for people with autism

The website will make a match between people and jobs, mainly in the graphical sector, but also other sectors.
The name of the company is novexa and automates jobs with people that are on the autism spectrum.
The whole matchmaking and feedback process and so doesn't have to be in this prototype, we just want the general information pages and to convey a great look and brand identity that we will keep in the other pages to be developed. The website must be made with Wordpress, since the backend will be developed in Wordpress too.
It is a social project that wants to create possibilites for people with ASS to work from home for an employer or to do a variety of tasks for different customers.
The people we hire are generally not on the regular job market or have difficulty finding a job and "selling themselves"

Target Market(s)

matchmaking between talent (with ASS) and employers / jobs

Number of Pages Required

5+ page

Font styles to use
Sans Serif

Colors
ec1f27
e34298
a64599
6b449b
0355a3
0792cd

Requirements
Must have
• A stunning landing pages
• Integrate our logo and must match with what will do. We want a clean, modern, minimalistic, sleek website that radiates creativity and good looks.
• We have one page describing what we can do for customers, one page for people with ASS that would like to be candidates (our approach, learning program, ...), two pages that are addressed to partners who want to cooperate: the one's that can assist with autism related assistance and the one's that can help with the job coaching.
Nice to have
• In our logo are many colors as we embrace diversity and want to show that. Out main branding colors are red (for action) and blue for stability and will all gradients that go with it. Mainly white or black (or anthracite) for other parts
Should not have
• We want a modern and minimalistic design, no fluffy designs with lots of ornaments.

```html
<!DOCTYPE html>
<html lang="en">
<head>
<meta charset="utf-8">
<title>Novexa – Work for people on the autism spectrum</title>
<link rel="stylesheet" href="https://fonts.googleapis.com/css2?family=Mulish:wght@400;600;700;800;900&display=swap">
<style>
:root{
  --red:#ec1f27;
  --pink:#e34298;
  --violet:#a64599;
  --purple:#6b449b;
  --purple-dark:#5a2e8c;
  --blue:#0355a3;
  --cyan:#0792cd;
  --hero-dark:#071b33;
  --hero-mid:#0d4677;
  --section-bg:#e9e9ef;
  --field-bg:#f3f3f3;
  --ink:#111111;
  --text:#222222;
  --white:#ffffff;
}
*{box-sizing:border-box;margin:0;padding:0}
html,body{width:1200px;height:2765px;overflow:hidden}
body{font-family:"Mulish",sans-serif;color:var(--text);background:var(--white);position:relative}

/* Hero */
.hero{position:absolute;left:0;top:0;width:1200px;height:634px;overflow:hidden}
.hero-media{position:absolute;inset:0;
  background:linear-gradient(180deg,#125d95 0%,var(--hero-mid) 45%,var(--hero-dark) 100%)}
.hero-play{position:absolute;left:570px;top:292px}
.brand-mark{position:absolute;left:200px;top:34px;width:48px;height:48px;background:var(--white);opacity:.9}
.brand{position:absolute;left:116px;top:96px;font-size:34px;font-weight:700;letter-spacing:4px;color:var(--white)}
.main-nav{position:absolute;top:26px;left:719px;display:flex;align-items:center}
.main-nav a{font-size:16px;color:var(--white);text-decoration:none;height:35px;line-height:35px}
.main-nav .is-active{background:var(--pink);border-radius:6px;width:73px;text-align:center;font-weight:800}
.main-nav .nav-about{margin-left:23px}
.main-nav .nav-services{margin-left:31px}
.main-nav .nav-contact{margin-left:35px}
.slider-arrow{position:absolute;top:256px}
.slider-arrow.prev{left:0}
.slider-arrow.next{right:0}

/* Welcome + services */
.intro{position:absolute;left:0;top:634px;width:1200px;height:1329px;background:var(--section-bg)}
.intro-title{position:absolute;left:96px;top:120px;font-size:48px;font-weight:900;color:var(--ink);letter-spacing:-.3px}
.intro-text{position:absolute;left:101px;top:198px;width:472px;font-size:13.6px;line-height:25.6px;color:var(--text)}
.btn{display:block;position:absolute;background:var(--purple-dark);color:var(--white);font-size:15px;font-weight:800;
  border-radius:6px;text-align:center;height:44px;line-height:44px;text-decoration:none;letter-spacing:.3px}
.intro .btn-learn{left:101px;top:377px;width:142px}
.intro-photo{position:absolute;left:630px;top:42px;width:454px;height:454px;border-radius:50%;
  background:linear-gradient(160deg,#6a5a55 0%,#3e4a3a 60%,#243322 100%)}
.mission-banner{position:absolute;left:105px;top:531px;width:990px;height:195px;border-radius:8px;
  background:linear-gradient(90deg,var(--cyan) 0%,var(--blue) 30%,var(--violet) 58%,var(--pink) 82%,var(--red) 100%);
  display:flex;align-items:center;justify-content:center;text-align:center}
.mission-banner p{color:var(--white);font-size:32px;font-weight:800;line-height:42px}
.services-title{position:absolute;left:0;width:1200px;top:778px;text-align:center;font-size:48px;font-weight:900;color:var(--ink)}
.service{position:absolute;top:924px;width:280px}
.service-icon{position:relative;height:66px}
.service-icon .halo{position:absolute;left:18px;top:0;width:62px;height:62px;border-radius:50%;background:#d6bdf0}
.service-icon svg{position:absolute;left:0;top:12px}
.service h3{margin-top:4px;font-size:29px;font-weight:900;color:var(--ink)}
.service p{margin-top:6px;font-size:13.6px;line-height:21px;color:var(--ink);width:262px}
.service .btn{position:relative;margin-top:18px;width:142px}

/* Contact */
.contact{position:absolute;left:0;top:1963px;width:1200px;height:619px;background:var(--white)}
.contact-title{position:absolute;left:0;width:1200px;top:60px;text-align:center;font-size:48px;font-weight:900;color:var(--ink)}
.field{position:absolute;background:var(--field-bg);font-size:17px;color:#333;padding-left:20px;line-height:50px;height:50px;width:434px}
.field.message{width:883px;height:140px;line-height:1;padding-top:26px}
.contact .btn-submit{left:531px;top:507px;width:140px}

/* Footer */
.site-footer{position:absolute;left:0;top:2582px;width:1200px;height:183px;background:var(--purple-dark)}
.social{position:absolute;top:49px;left:530px;display:flex;gap:37px}
.social span{display:block;width:20px;height:20px;border-radius:50%;background:var(--white)}
.copyright{position:absolute;top:101px;width:1200px;text-align:center;color:var(--white);font-size:14px;letter-spacing:.3px}
</style>
</head>
<body>

<header class="hero">
  <div class="hero-media" role="img" aria-label="Hero video still in deep blue tones"></div>
  <svg class="hero-play" width="62" height="80" viewBox="0 0 62 80" aria-label="Play video"><polygon points="3,3 58,40 3,77" fill="none" stroke="#fff" stroke-width="4"/></svg>
  <span class="brand-mark"></span>
  <div class="brand">NOVEXA</div>
  <nav class="main-nav">
    <a class="is-active" href="#">Home</a>
    <a class="nav-about" href="#">About Us</a>
    <a class="nav-services" href="#">Services</a>
    <a class="nav-contact" href="#">Contact Us</a>
  </nav>
  <svg class="slider-arrow prev" width="44" height="60" viewBox="0 0 44 60" aria-label="Previous slide"><polygon points="0,0 44,30 0,60" fill="#0b6fb8"/><polyline points="16,24 10,30 16,36" fill="none" stroke="#fff" stroke-width="3"/></svg>
  <svg class="slider-arrow next" width="44" height="60" viewBox="0 0 44 60" aria-label="Next slide"><polygon points="44,0 0,30 44,60" fill="#6b449b"/><polyline points="26,24 32,30 26,36" fill="none" stroke="#fff" stroke-width="3"/></svg>
</header>

<main>
<section class="intro">
  <h1 class="intro-title">Welcome To Novexa</h1>
  <p class="intro-text">Lorem ipsum dolor sit amet, consectetur adipiscing elit, sed do eiusmod tempor incididunt ut labore et dolore magna aliqua. Ut enim ad minim veniam, quis nostrud exercitation ullamco laboris nisi ut aliquip ex ea commodo consequat. Duis aute irure dolor in reprehenderit in voluptate velit esse cillum dolore eu fugiat nulla pariatur. Excepteur sint occaecat cupidatat non proident, sunt in culpa qui officia deserunt mollit anim id est laborum.</p>
  <a class="btn btn-learn" href="#">LEARN MORE</a>
  <div class="intro-photo" role="img" aria-label="Photo of a smiling young man working at a desk with papers"></div>

  <div class="mission-banner">
    <p>People with autism spectrum. to work from home the work<br>can be&nbsp; variety of tasks for different customers.</p>
  </div>

  <h2 class="services-title">Our Services</h2>

  <article class="service" style="left:131px">
    <div class="service-icon"><span class="halo"></span>
      <svg width="56" height="44" viewBox="0 0 56 44"><g fill="#5a2e8c"><circle cx="28" cy="10" r="8"/><circle cx="12" cy="14" r="6"/><circle cx="44" cy="14" r="6"/><path d="M14 40c0-10 6-16 14-16s14 6 14 16z"/><path d="M0 38c0-8 5-12 11-12 2 0 4 1 5 2-3 3-4 6-4 10z"/><path d="M56 38c0-8-5-12-11-12-2 0-4 1-5 2 3 3 4 6 4 10z"/></g></svg>
    </div>
    <h3>Lorem Ipsum</h3>
    <p>Lorem ipsum dolor sit amet, consectetur adipiscing elit, sed do eiusmod tempor incididunt ut labore et dolore magna aliqua. Ut enim ad minim veniam,</p>
    <a class="btn" href="#">LEARN MORE</a>
  </article>

  <article class="service" style="left:464px">
    <div class="service-icon"><span class="halo"></span>
      <svg width="52" height="40" viewBox="0 0 52 40"><g fill="#5a2e8c"><path d="M6 2h40v26H6zM10 6v18h32V6z" fill-rule="evenodd"/><rect x="0" y="31" width="52" height="5" rx="2"/></g></svg>
    </div>
    <h3>Lorem Ipsum</h3>
    <p>Lorem ipsum dolor sit amet, consectetur adipiscing elit, sed do eiusmod tempor incididunt ut labore et dolore magna aliqua. Ut enim ad minim veniam,</p>
    <a class="btn" href="#">LEARN MORE</a>
  </article>

  <article class="service" style="left:816px">
    <div class="service-icon"><span class="halo"></span>
      <svg width="44" height="44" viewBox="0 0 44 44"><g fill="#5a2e8c"><circle cx="22" cy="22" r="14"/><rect x="18" y="2" width="8" height="10"/><rect x="18" y="32" width="8" height="10"/><rect x="2" y="18" width="10" height="8"/><rect x="32" y="18" width="10" height="8"/><g transform="rotate(45 22 22)"><rect x="18" y="2" width="8" height="10"/><rect x="18" y="32" width="8" height="10"/><rect x="2" y="18" width="10" height="8"/><rect x="32" y="18" width="10" height="8"/></g></g><circle cx="22" cy="22" r="5" fill="#d6bdf0"/></svg>
    </div>
    <h3>Lorem Ipsum</h3>
    <p>Lorem ipsum dolor sit amet, consectetur adipiscing elit, sed do eiusmod tempor incididunt ut labore et dolore magna aliqua. Ut enim ad minim veniam,</p>
    <a class="btn" href="#">LEARN MORE</a>
  </article>
</section>

<section class="contact">
  <h2 class="contact-title">Contact Us</h2>
  <div class="field" style="left:158px;top:158px">First Name</div>
  <div class="field" style="left:608px;top:158px">Last Name</div>
  <div class="field" style="left:158px;top:237px">Email</div>
  <div class="field" style="left:608px;top:237px">Phone</div>
  <div class="field message" style="left:158px;top:317px">Message</div>
  <a class="btn btn-submit" href="#">SUBMIT</a>
</section>
</main>

<footer class="site-footer">
  <div class="social">
    <span aria-label="Social link one"></span>
    <span aria-label="Social link two"></span>
    <span aria-label="Social link three"></span>
  </div>
  <p class="copyright">© 2019 &nbsp;| &nbsp;WWW.NOVEXAWORK.COM</p>
</footer>

</body>
</html>
```